New, modern business card for growing audiology practice

We need a new business card for our audiology practice. Our logo and website have recently changed (more modern) and we want our business cards to reflect this change.
We conduct hearing tests, perform earwax removals, and fit & dispense hearing aids to our patients. We are a family owned practice in which the owner is the one who works directly with the patient. I have attached logos in various formats to use, as well as two ideas I found on this website; as well as a scanned copy of our current logo. Good luck!

Industry/Entity Type

Business

Contact Information for Business Card

Company name: Tolvera Hearing Center
Provider name: Peter Wolstenby, Au.D. F/NSB
Phone number: (555) 683-5127
Address: 837 W. Lindell Ave. Brenwick Falls, NY 14872
email: tolverahearing@postvane.com
website: tolverahearing.com

Colors
000000
aaaaaa
dbdbdb
cacaca
9bcb3c
afd23c
cadf82
b1b1b1

Requirements
Must have
• My card must include information in the "details" section. In the attached images, I found a few that I liked and I would like to model after - "brisky bouncin'" and "Sound Method Center".
• Must be horizontal.
• Must include logos provided. I uploaded them in various file formats and various ways.
• Must match logo font, if possible, if not, please get as close as you can.
Nice to have
• I really like the idea of having a color on one side with just the logo and company name and the contact information and provider name on the other side. I also really like the idea of having the main color dominating on the logo/company side with accent of that same color on the contact side of the card.
Should not have
• Must not be vertical.

```html
<!DOCTYPE html>
<html lang="en">
<head>
<meta charset="utf-8">
<title>Tolvera Hearing Center – Business Card</title>
<link href="https://fonts.googleapis.com/css2?family=Lato:wght@400&family=Roboto:wght@400;500&family=Roboto+Condensed:wght@700&display=swap" rel="stylesheet">
<style>
  :root {
    --backdrop: #ecebe8;
    --card-dark: #191b1c;
    --card-light: #f3f3f3;
    --green: #6f9e3a;
    --ink: #1a1a1a;
    --text-grey: #4a4a4a;
    --rule: #555555;
    --white: #ffffff;
  }
  * { margin: 0; padding: 0; box-sizing: border-box; }
  html, body { width: 1200px; height: 960px; overflow: hidden; }
  body { background: var(--backdrop); position: relative; font-family: "Roboto", sans-serif; }

  .card { position: absolute; width: 600px; height: 342px; border-radius: 18px; overflow: hidden; }

  /* front side */
  .card-front { left: 322px; top: 108px; background: var(--card-dark); }
  .brand { position: absolute; display: flex; align-items: center; gap: 10px; font-family: "Lato", sans-serif; font-weight: 400; white-space: nowrap; letter-spacing: -0.3px; }
  .brand-dot { border-radius: 50%; background: var(--green); flex: none; }
  .card-front .brand { left: 0; right: 0; top: 152px; justify-content: center; font-size: 29px; color: var(--white); }
  .card-front .brand-dot { width: 22px; height: 22px; }
  .front-web { position: absolute; left: 0; right: 0; top: 286px; text-align: center; color: var(--white); font-size: 14px; letter-spacing: 3.4px; }

  /* back side */
  .card-back { left: 320px; top: 493px; background: var(--card-light); }
  .edge-band { position: absolute; left: 0; top: 0; width: 12px; height: 100%; background: #000; }
  .edge-tab { position: absolute; left: 0; top: 0; }
  .provider-name { position: absolute; left: 28px; top: 44px; font-family: "Roboto Condensed", sans-serif; font-weight: 700; font-size: 20px; color: var(--green); }
  .provider-title { position: absolute; left: 28px; top: 72px; font-family: "Roboto", sans-serif; font-weight: 500; font-size: 15px; color: var(--ink); }
  .card-back .brand { right: 30px; top: 56px; font-size: 21px; color: var(--ink); gap: 8px; }
  .card-back .brand-dot { width: 16px; height: 16px; }
  .header-rule { position: absolute; left: 28px; right: 30px; top: 100px; height: 1.5px; background: var(--rule); }

  .contact-list { position: absolute; left: 28px; top: 240px; list-style: none; }
  .contact-list li { display: flex; align-items: center; gap: 8px; font-size: 15px; line-height: 19.5px; color: var(--text-grey); }
  .contact-list svg { width: 14px; height: 14px; flex: none; }
  .address { position: absolute; right: 28px; top: 260px; text-align: right; font-size: 15px; line-height: 19.5px; color: var(--text-grey); font-style: normal; }
</style>
</head>
<body>

<section class="card card-front" aria-label="Card front">
  <div class="brand"><span class="brand-dot"></span>TOLVERA HEARING CENTER</div>
  <p class="front-web">www.tolverahearing.com</p>
</section>

<section class="card card-back" aria-label="Card back">
  <div class="edge-band"></div>
  <svg class="edge-tab" width="14" height="342" viewBox="0 0 14 342">
    <polygon points="0,48 14,40 14,92 0,100" fill="var(--green)"/>
  </svg>

  <h1 class="provider-name">PETER WOLSTENBY</h1>
  <p class="provider-title">AU.D. F/NSB</p>
  <div class="brand"><span class="brand-dot"></span>TOLVERA HEARING CENTER</div>
  <div class="header-rule"></div>

  <ul class="contact-list">
    <li>
      <svg viewBox="0 0 24 24"><path fill="var(--green)" d="M6.6 10.8a15.1 15.1 0 0 0 6.6 6.6l2.2-2.2c.3-.3.7-.4 1-.2 1.1.4 2.3.6 3.6.6.6 0 1 .4 1 1V20c0 .6-.4 1-1 1A17 17 0 0 1 3 4c0-.6.4-1 1-1h3.5c.6 0 1 .4 1 1 0 1.3.2 2.5.6 3.6.1.3 0 .7-.2 1z"/></svg>
      (555) 683-5127
    </li>
    <li>
      <svg viewBox="0 0 24 24"><rect x="2" y="5" width="20" height="14" rx="1.5" fill="var(--green)"/><path d="M3 6l9 7 9-7" fill="none" stroke="var(--card-light)" stroke-width="1.8"/></svg>
      tolverahearing@postvane.com
    </li>
    <li>
      <svg viewBox="0 0 24 24"><circle cx="12" cy="12" r="10" fill="var(--green)"/><path d="M2 12h20M12 2c3 3 3 17 0 20M12 2c-3 3-3 17 0 20" fill="none" stroke="var(--card-light)" stroke-width="1.4"/></svg>
      tolverahearing.com
    </li>
  </ul>

  <address class="address">837 W. Lindell Ave.<br>Brenwick Falls, NY 14872</address>
</section>

</body>
</html>
```